corvale institute of business and technology web site

I need web site for the institute which focus on business courses and computer course it is also for vocation train for employment It is also carear development and advancement .It should have links to online study resource which free
Industry/Entity Type
Business
Number of Pages Required
1 page
Look and feel
Each slider illustrates characteristics of the customer's brand and the style your logo design should communicate.

```html
<!DOCTYPE html>
<html lang="en">
<head>
<meta charset="utf-8">
<title>Corvale Institute of Business and Technology</title>
<link href="https://fonts.googleapis.com/css2?family=Open+Sans:wght@300;400;600;700&display=swap" rel="stylesheet">
<style>
  :root {
    --brand-blue: #1a8fd8;
    --brand-blue-dark: #0f5fa8;
    --navy: #1b2a6b;
    --navy-deep: #141d4f;
    --ink: #2b2b2b;
    --muted: #6b6b6b;
    --light: #f2f2f2;
    --white: #ffffff;
    --footer: #1e1e1e;
    --tick: #1a8fd8;
  }
  * { margin: 0; padding: 0; box-sizing: border-box; }
  html, body { width: 700px; height: 1200px; overflow: hidden; }
  body { font-family: "Open Sans", Arial, sans-serif; color: var(--ink); background: var(--white); position: relative; }

  .site-header { position: absolute; top: 0; left: 0; width: 700px; height: 65px; background: var(--white); z-index: 3; }
  .brand-badge { position: absolute; left: 30px; top: 0; width: 86px; height: 96px; background: var(--brand-blue);
    display: flex; flex-direction: column; align-items: center; justify-content: center; gap: 6px; padding: 8px; }
  .brand-badge .mark { width: 22px; height: 22px; border-radius: 50%; background: var(--white); }
  .brand-badge .name { color: var(--white); font-size: 9px; font-weight: 600; text-align: center; line-height: 1.25; text-transform: uppercase; }
  .main-nav { position: absolute; right: 18px; top: 30px; display: flex; gap: 6px; }
  .main-nav a { font-size: 10px; color: var(--ink); text-decoration: none; padding: 5px 9px; text-transform: uppercase; letter-spacing: .3px; }
  .main-nav a.active { border: 1px solid var(--brand-blue); color: var(--brand-blue); }

  .hero { position: absolute; top: 65px; left: 0; width: 700px; height: 337px; }
  .hero-photo { position: absolute; inset: 0; background: linear-gradient(100deg, #b9c9a8 0%, #e9ede2 30%, #f4f2ee 55%, #d8d4cb 100%); }
  .hero-banner { position: absolute; right: 0; top: 190px; width: 318px; padding: 12px 20px 14px; background: rgba(20,29,79,.88); color: var(--white); text-transform: uppercase; }
  .hero-banner .lead { font-size: 12px; font-weight: 400; letter-spacing: .5px; }
  .hero-banner .big { font-size: 21px; font-weight: 400; line-height: 1.15; margin-top: 2px; }
  .hero-arrows { position: absolute; right: 46px; top: 240px; display: flex; gap: 5px; }
  .hero-arrows span { width: 18px; height: 18px; border-radius: 50%; background: #222; display: flex; align-items: center; justify-content: center; }

  .about { position: absolute; top: 402px; left: 0; width: 700px; height: 176px; text-align: center; }
  .section-title { font-size: 24px; font-weight: 300; letter-spacing: 1px; text-transform: uppercase; }
  .section-title strong { font-weight: 700; }
  .about .section-title { margin-top: 32px; color: var(--ink); }
  .title-rule { width: 40px; height: 2px; background: var(--brand-blue); margin: 4px auto 0; }
  .about p { width: 540px; margin: 10px auto 0; font-size: 8.5px; line-height: 1.6; color: var(--muted); }
  .btn { display: inline-block; background: var(--brand-blue); color: var(--white); font-size: 8px; text-transform: uppercase; padding: 4px 12px; letter-spacing: .4px; }
  .about .btn { margin-top: 10px; }

  .programs { position: absolute; top: 578px; left: 0; width: 700px; height: 297px; background: linear-gradient(135deg, #2a3c8f 0%, #1b2a6b 45%, #2c3f96 70%, #1d2c72 100%); text-align: center; color: var(--white); }
  .programs .section-title { margin-top: 34px; }
  .program-grid { position: absolute; top: 68px; left: 42px; width: 618px; display: flex; justify-content: space-between; }
  .program-card { width: 145px; }
  .program-image { width: 145px; height: 94px; }
  .program-card h3 { font-size: 9px; font-weight: 700; margin-top: 10px; text-transform: uppercase; letter-spacing: .3px; }
  .program-card p { font-size: 8px; line-height: 1.45; margin-top: 4px; padding: 0 8px; color: #dfe4f5; }
  .program-card .btn { margin-top: 10px; padding: 3px 10px; }

  .technology { position: absolute; top: 875px; left: 0; width: 700px; height: 268px; background: var(--light); }
  .tech-image { position: absolute; left: 42px; top: 52px; width: 232px; height: 168px; background: linear-gradient(120deg, #e8e8e8, #cfd3d8 60%, #b8bec6); }
  .tech-play { position: absolute; left: 134px; top: 118px; width: 40px; height: 40px; border-radius: 50%; background: rgba(0,0,0,.55); display: flex; align-items: center; justify-content: center; }
  .tech-copy { position: absolute; left: 303px; top: 50px; width: 370px; }
  .tech-copy .section-title { font-size: 22px; color: var(--ink); }
  .tech-copy .section-title strong { color: var(--brand-blue-dark); }
  .tech-copy h3 { font-size: 11px; font-weight: 700; margin-top: 8px; text-transform: uppercase; }
  .tech-list { list-style: none; margin-top: 6px; }
  .tech-list li { display: flex; align-items: center; gap: 7px; font-size: 8.5px; line-height: 1; height: 17px; color: #444; }
  .tech-list svg { flex: none; }

  .site-footer { position: absolute; top: 1143px; left: 0; width: 700px; height: 57px; background: var(--footer); color: #aaa; font-size: 8px; display: flex; align-items: center; justify-content: space-between; padding: 0 42px; }
  .social { display: flex; gap: 5px; }
  .social span { width: 15px; height: 15px; border-radius: 50%; background: #e6e6e6; }
</style>
</head>
<body>
  <header class="site-header">
    <div class="brand-badge">
      <span class="mark"></span>
      <span class="name">Corvale Institute</span>
    </div>
    <nav class="main-nav">
      <a class="active" href="#">Home</a>
      <a href="#">Services</a>
      <a href="#">Testimonials</a>
      <a href="#">Clients</a>
      <a href="#">About Us</a>
      <a href="#">Contact</a>
    </nav>
  </header>

  <section class="hero">
    <div class="hero-photo" role="img" aria-label="Smiling student in an orange top working on a laptop in a bright room"></div>
    <div class="hero-banner">
      <div class="lead">We are an institute which focus</div>
      <div class="big">on Business Courses &amp;<br>Computer Course</div>
    </div>
    <div class="hero-arrows">
      <span><svg width="8" height="8" viewBox="0 0 8 8"><path d="M5 1L2 4l3 3" stroke="#fff" stroke-width="1.4" fill="none"/></svg></span>
      <span><svg width="8" height="8" viewBox="0 0 8 8"><path d="M3 1l3 3-3 3" stroke="#fff" stroke-width="1.4" fill="none"/></svg></span>
    </div>
  </section>

  <section class="about">
    <h2 class="section-title">About <strong>CIBT</strong></h2>
    <div class="title-rule"></div>
    <p>Corvale Institute of Business and Technology (CIBT) is a fast-growing Education &amp; Training Solution Provider, focusing on holistic knowledge and skills interventions that impact livelihoods. It is established on the core values of creating a meaningful and measurable difference on career aspirations and goals through innovative learning and knowledge management intervention.</p>
    <span class="btn">Learn More</span>
  </section>

  <section class="programs">
    <h2 class="section-title">Our <strong>Programs Offered</strong></h2>
    <div class="program-grid">
      <article class="program-card">
        <div class="program-image" role="img" aria-label="Group of university students smiling together" style="background:linear-gradient(135deg,#c9d6e6,#8fa6c4)"></div>
        <h3>University Education</h3>
        <p>Lorem ipsum dolor sit amet, consectetur adipiscing elit, sed do ei dolore magna aliqua</p>
        <span class="btn">More</span>
      </article>
      <article class="program-card">
        <div class="program-image" role="img" aria-label="Collage of soft skill icons on a light backdrop" style="background:linear-gradient(135deg,#e3e6ea,#9fb0c2)"></div>
        <h3>Modular Soft Skills</h3>
        <p>Lorem ipsum dolor sit amet, consectetur adipiscing elit, sed do ei dolore magna aliqua</p>
        <span class="btn">More</span>
      </article>
      <article class="program-card">
        <div class="program-image" role="img" aria-label="Hands using a tablet device" style="background:linear-gradient(135deg,#e9eef3,#a8bccf)"></div>
        <h3>Direct to Device</h3>
        <p>Lorem ipsum dolor sit amet, consectetur adipiscing elit, sed do ei dolore magna aliqua</p>
        <span class="btn">More</span>
      </article>
      <article class="program-card">
        <div class="program-image" role="img" aria-label="Business professionals in a meeting" style="background:linear-gradient(135deg,#d8dde3,#7d8da3)"></div>
        <h3>Business Verticals</h3>
        <p>Lorem ipsum dolor sit amet, consectetur adipiscing elit, sed do ei dolore magna aliqua</p>
        <span class="btn">More</span>
      </article>
    </div>
  </section>

  <section class="technology">
    <div class="tech-image" role="img" aria-label="Video lesson still of a presenter at a computer"></div>
    <span class="tech-play"><svg width="14" height="14" viewBox="0 0 14 14"><path d="M4 2l8 5-8 5z" fill="#fff"/></svg></span>
    <div class="tech-copy">
      <h2 class="section-title">Technology <strong>Capabilities</strong></h2>
      <h3>Live Video Learning</h3>
      <ul class="tech-list">
        <li><svg width="10" height="10" viewBox="0 0 10 10"><circle cx="5" cy="5" r="5" fill="var(--tick)"/><path d="M2.6 5.2l1.6 1.5 3.2-3.3" stroke="#fff" stroke-width="1.2" fill="none"/></svg>Robust remote video learning infrastructure – HD Video quality at Home Broad Band</li>
        <li><svg width="10" height="10" viewBox="0 0 10 10"><circle cx="5" cy="5" r="5" fill="var(--tick)"/><path d="M2.6 5.2l1.6 1.5 3.2-3.3" stroke="#fff" stroke-width="1.2" fill="none"/></svg>Common Platform for disseminating corporate news, Product update</li>
        <li><svg width="10" height="10" viewBox="0 0 10 10"><circle cx="5" cy="5" r="5" fill="var(--tick)"/><path d="M2.6 5.2l1.6 1.5 3.2-3.3" stroke="#fff" stroke-width="1.2" fill="none"/></svg>Uniformity of lesson content</li>
        <li><svg width="10" height="10" viewBox="0 0 10 10"><circle cx="5" cy="5" r="5" fill="var(--tick)"/><path d="M2.6 5.2l1.6 1.5 3.2-3.3" stroke="#fff" stroke-width="1.2" fill="none"/></svg>Interactive learning experience, Live Doubt Classroom/Virtual Social Learning</li>
        <li><svg width="10" height="10" viewBox="0 0 10 10"><circle cx="5" cy="5" r="5" fill="var(--tick)"/><path d="M2.6 5.2l1.6 1.5 3.2-3.3" stroke="#fff" stroke-width="1.2" fill="none"/></svg>Robust Social learning Platform: Remote access anywhere and anytime</li>
        <li><svg width="10" height="10" viewBox="0 0 10 10"><circle cx="5" cy="5" r="5" fill="var(--tick)"/><path d="M2.6 5.2l1.6 1.5 3.2-3.3" stroke="#fff" stroke-width="1.2" fill="none"/></svg>Offline video and interactive course content – help to transfer boundaries</li>
        <li><svg width="10" height="10" viewBox="0 0 10 10"><circle cx="5" cy="5" r="5" fill="var(--tick)"/><path d="M2.6 5.2l1.6 1.5 3.2-3.3" stroke="#fff" stroke-width="1.2" fill="none"/></svg>Experiential Learning</li>
      </ul>
    </div>
  </section>

  <footer class="site-footer">
    <span>Copyright (c) 2015, Corvale All Right Reserved</span>
    <div class="social"><span></span><span></span><span></span><span></span><span></span><span></span></div>
  </footer>
</body>
</html>
```